Business Card for Coastal Tundrabridge Advisory

We need a business card for Coastal Tundrabridge Advisory. The company website address is provided below. The company logo is attached. We provide specialized permafrost services to the mining, transportation, and oil & gas industries. The card should be prepared for:
Matthias Korhonen, PhD.
Coastal Tundrabridge Advisory
PO Box 418259
Quillwater, Alaska 99642
Direct: +1-907-555-0143
Email: mkorhonen@tundrabridgeadvisory.example
Website: www.coastaltundrabridgeadvisory.example

```html
<!DOCTYPE html>
<html lang="en">
<head>
<meta charset="utf-8">
<title>Coastal Tundrabridge Advisory — Business Card</title>
<link href="https://fonts.googleapis.com/css2?family=Open+Sans:ital,wght@1,700&family=PT+Sans+Narrow:wght@700&display=swap" rel="stylesheet">
<style>
  :root {
    --backdrop: #eeeeee;
    --card-front: #ffffff;
    --card-back: #3a3a3a;
    --ink: #222222;
    --frame: #7a7a7a;
    --icon: #555555;
    --mark: #141414;
  }
  html, body {
    margin: 0;
    padding: 0;
    width: 1200px;
    height: 1199px;
    overflow: hidden;
    background: var(--backdrop);
  }
  .canvas {
    position: relative;
    width: 1200px;
    height: 1199px;
  }
  .card {
    position: absolute;
    border-radius: 28px;
    overflow: hidden;
  }
  .card-front {
    left: 243px; top: 156px;
    width: 724px; height: 411px;
    background: var(--card-front);
    color: var(--ink);
    font-family: "PT Sans Narrow", "Arial Narrow", sans-serif;
    font-weight: 700;
  }
  .frame {
    position: absolute;
    left: 0; top: 0;
  }
  .identity {
    position: absolute;
    right: 384px;
    top: 324px;
    top: 168px;
    text-align: right;
  }
  .person-name {
    font-family: "Open Sans", Arial, sans-serif;
    font-style: italic;
    font-weight: 700;
    font-size: 20px;
    letter-spacing: -0.3px;
    margin: 0;
    line-height: 1.2;
  }
  .person-role {
    font-family: "Open Sans", Arial, sans-serif;
    font-style: italic;
    font-weight: 700;
    font-size: 8px;
    margin: 6px 0 0;
  }
  .divider {
    position: absolute;
    left: 361px; top: 124px;
    width: 1.5px; height: 135px;
    background: var(--ink);
  }
  .contact-list {
    position: absolute;
    left: 374px; top: 143px;
    margin: 0; padding: 0;
    list-style: none;
  }
  .contact-list li {
    display: flex;
    align-items: center;
    height: 27px;
    font-size: 14.5px;
  }
  .contact-list svg {
    width: 20px; height: 20px;
    margin-right: 8px;
    flex: none;
  }
  .postal {
    position: absolute;
    left: 0; right: 0; top: 350px;
    text-align: center;
    font-size: 14px;
    line-height: 21px;
  }
  .card-back {
    left: 236px; top: 648px;
    width: 724px; height: 413px;
    background: var(--card-back);
    display: flex;
    align-items: center;
    justify-content: center;
  }
  .brand-name {
    font-family: "PT Sans Narrow", "Arial Narrow", sans-serif;
    font-weight: 700;
    font-size: 40px;
    letter-spacing: 4px;
    text-transform: uppercase;
    color: var(--mark);
    margin: 0;
  }
</style>
</head>
<body>
<main class="canvas">
  <section class="card card-front" aria-label="Card front">
    <svg class="frame" width="724" height="411" viewBox="0 0 724 411" aria-hidden="true">
      <path d="M148 373 H44 a25 25 0 0 1 -25 -25 V40 a25 25 0 0 1 25 -25 H680 a25 25 0 0 1 25 25 V348 a25 25 0 0 1 -25 25 H575"
            fill="none" stroke="var(--frame)" stroke-width="2.5"/>
    </svg>

    <div class="identity">
      <h1 class="person-name">Matthias Korhonen, PhD</h1>
      <p class="person-role">Founder &amp; Director</p>
    </div>

    <div class="divider"></div>

    <ul class="contact-list">
      <li>
        <svg viewBox="0 0 20 20" aria-hidden="true"><circle cx="10" cy="10" r="8.5" fill="none" stroke="var(--icon)" stroke-width="1.3"/><path d="M7 6 l1.6 -0.3 1 2.2 -1 .8 a6 6 0 0 0 2.8 2.8 l.8 -1 2.2 1 -.3 1.6 c-3.5 .5 -7.6 -3.6 -7.1 -7.1z" fill="var(--icon)"/></svg>
        +1-907-555-0143
      </li>
      <li>
        <svg viewBox="0 0 20 20" aria-hidden="true"><circle cx="10" cy="10" r="8.5" fill="none" stroke="var(--icon)" stroke-width="1.3"/><rect x="7" y="5" width="6" height="10" rx="1" fill="none" stroke="var(--icon)" stroke-width="1.2"/></svg>
        (907) 555 0143
      </li>
      <li>
        <svg viewBox="0 0 20 20" aria-hidden="true"><circle cx="10" cy="10" r="9" fill="var(--icon)"/><rect x="5.5" y="7" width="9" height="6.5" fill="#fff"/><path d="M5.5 7 L10 10.5 L14.5 7" fill="none" stroke="var(--icon)" stroke-width="1"/></svg>
        mkorhonen@tundrabridgeadvisory.example
      </li>
      <li>
        <svg viewBox="0 0 20 20" aria-hidden="true"><circle cx="10" cy="10" r="8.5" fill="none" stroke="var(--icon)" stroke-width="1.3"/><circle cx="10" cy="10" r="5" fill="none" stroke="var(--icon)" stroke-width="1"/><ellipse cx="10" cy="10" rx="2.2" ry="5" fill="none" stroke="var(--icon)" stroke-width="1"/><path d="M5 10 H15" stroke="var(--icon)" stroke-width="1"/></svg>
        www.coastaltundrabridgeadvisory.example
      </li>
    </ul>

    <address class="postal" style="font-style:normal">
      PO Box 418259<br>
      Quillwater, Alaska 99642
    </address>
  </section>

  <section class="card card-back" aria-label="Card back">
    <p class="brand-name">Coastal Tundrabridge Advisory</p>
  </section>
</main>
</body>
</html>
```